Home Page Design for Motor Manufacturer

Hello,
please design the homepage for a manufacturer of industry motors. I am looking for a professional, clean and minimalistic design. Since this a rather conservative industry it should get a professional look but since it is a redesign there should be some modern that gives is the modern touch of innovation.
A competitor's homepage I like is:
https://www.valdorix.example/en/
What I like about this website:
* clean, minimal, well structured design
* mega menu
For this project please find attached the wireframes (most buttons are in German but by context and Google translate you will easily figure it out; only unclear - "Messe" means "trade exhibition"). The paddings and margins are NOT exact. Also any color of backgrounds etc. chosen is not meant to represent a real color but rather to illustrate the object and maybe show there should be some background emphasis (color or image).
Wireframes:
https: //www.filnest. example / t / pQmW7zKtRb3LyaHx
In both wireframes the only thing that is different is the Service section. I expect from the winner both designs for this service section: one with normal cart design and one with tabs as filters to search products (find image for product categories attached)
In the header use on the left the following text:
h1: "Your competent partner for industrial engines,
-transmission and drawing parts
with more than 5000 satisfied customers "
primary button: Our products
sec. button: Download catalog
and on the right side we feature one or more product images (like putting them in a nice display together).
I also think of a solid background color or subtle gradient for the hero section.
The winner should also design an open mega menu version.
Menu items in this order:
• Home page
• Gearboxes & Motors
• Engine components
• Drawing parts
• Machines & accessories
• About us
• Contact
Also create a language switch with globe symbol and DE for Germany and EN for English above the nav plus the telephone number with icon (user dummy number +49 (0) 987654321)
Output should be in Figma, Sketch or PSD.
Fonts + color to use:
header: Proza Libre, bold, # 0171A1
body: Open Sans, regular, black
Primary accent color: # 0171A1
Text black or dark gray
background: light gray, white or shade of blue
More image resources:
https://www.filnest.example/t/ZuTn4VcqMh8ErwJo
If there are any questions please do not hesitate to ask.
Target Market(s)
B2B - anyone with industrial machinery needing small motors (not car engines)
Industry/Entity Type
Manufacturing
Number of Pages Required
1 page
Requirements
Must have
- see above
Nice to have
- see above
Should not have
- see above

```html
<!DOCTYPE html>
<html lang="en">
<head>
<meta charset="utf-8">
<title>Korven – Homepage</title>
<link href="https://fonts.googleapis.com/css2?family=Proza+Libre:wght@400;600;700;800&family=Open+Sans:wght@400;600;700&display=swap" rel="stylesheet">
<style>
:root{
  --accent:#0171a1;
  --navy:#0b4f7c;
  --deep:#0a3d63;
  --sky:#1a86b8;
  --cyan:#45b2cf;
  --hero:#eef0f2;
  --ink:#1b1b1b;
  --grey:#555;
  --line:#dfe3e7;
  --foot:#262626;
  --board:#cbd7e3;
}
*{box-sizing:border-box;margin:0;padding:0}
html,body{width:708px;height:1200px;overflow:hidden}
body{background:var(--board);font-family:"Open Sans",sans-serif;color:var(--ink);position:relative}
.frame{position:absolute;top:49px;width:299px;height:1102px;overflow:hidden;box-shadow:0 2px 8px rgba(0,0,0,.18)}
.frame--home{left:45px}
.frame--mega{left:364px}
.page{position:absolute;left:0;top:0;width:627px;height:2309px;background:#fff;transform:scale(.4771);transform-origin:0 0}
.page *{position:absolute}
.page p,.page span,.page li,.page h1,.page h2,.page h3,.page a{white-space:nowrap}
h1,h2,h3,.brand{font-family:"Proza Libre",sans-serif}

/* header */
.topbar{left:0;top:0;width:627px;height:50px;background:#fff}
.brand{left:76px;top:11px;font-size:26px;font-weight:800;color:var(--navy);letter-spacing:1px}
.call{left:338px;top:13px;width:130px;height:26px}
.call svg{left:0;top:1px}
.call .lbl{left:28px;top:0;font-size:7px;color:var(--accent)}
.call .num{left:28px;top:9px;font-size:10px;font-weight:700;color:var(--deep)}
.lang{left:476px;top:16px;width:54px;height:18px;border:1px solid #c8ccd0;border-radius:9px;font-size:7px;color:#555}
.lang svg{left:9px;top:4px}
.lang span{left:22px;top:3px}
.lang i{left:39px;top:4px;width:4px;height:4px;border-right:1px solid #777;border-bottom:1px solid #777;transform:rotate(45deg)}
.search{left:538px;top:18px}
.nav{left:0;top:50px;width:627px;height:27px;background:linear-gradient(90deg,#0c5e93,#1a86b8 55%,#0c5e93)}
.nav a{top:0;height:27px;line-height:27px;font-size:7px;font-weight:700;color:#fff;padding:0 8px;position:absolute;text-decoration:none}
.nav a.is-active{background:var(--deep)}

/* hero */
.hero{left:0;top:77px;width:627px;height:360px;background:radial-gradient(circle at 12% 85%,#dfe2e5 0,transparent 35%),linear-gradient(180deg,#f6f7f8,var(--hero))}
.hero h1{left:76px;top:88px;font-size:15.5px;line-height:20px;font-weight:800;color:var(--navy);white-space:normal;width:240px;position:absolute}
.hero .sub{left:76px;top:130px;font-size:15px;line-height:20px;font-family:"Proza Libre",sans-serif;white-space:normal;width:220px;color:#222}
.btn{height:24px;line-height:24px;border-radius:12px;color:#fff;font-size:7.5px;font-weight:700;text-align:center;font-family:"Open Sans",sans-serif}
.btn--accent{background:var(--accent)}
.btn--navy{background:var(--deep)}
.btn--sky{background:var(--sky)}
.hero .b1{left:76px;top:206px;width:94px}
.hero .b2{left:176px;top:206px;width:115px}
.hero-visual{left:340px;top:48px;width:215px;height:227px;border-radius:50%;background:radial-gradient(circle,#5c6066 0 14%,#b9bdc2 15% 38%,#8c9197 39% 60%,#d8dadd 61% 100%)}
.thumb{top:305px;width:115px;height:101px;background:#fafbfc;border:1px solid var(--line)}
.thumb div{left:25px;top:18px;width:65px;height:65px;border-radius:6px;background:linear-gradient(135deg,#3a3f46,#9aa0a6)}
.thumb--active{top:301px;background:var(--cyan);border-color:var(--cyan);box-shadow:0 6px 10px rgba(0,0,0,.2)}
.thumb--active div{border-radius:50%;background:radial-gradient(circle,#6b7077,#c9ccd0)}
.arrow{top:354px}

/* products */
.section-title{width:627px;left:0;text-align:center;font-size:20px;font-weight:700;color:#111}
.rule{left:298px;width:30px;height:2px;background:var(--accent)}
.prod{width:240px;height:141px;border:1px solid var(--line);border-radius:4px;background:#fff;overflow:hidden}
.prod .img{left:0;top:0;width:106px;height:141px;background:linear-gradient(135deg,#7cc6ea,#2f8fc7)}
.prod h3{left:106px;width:134px;top:16px;text-align:center;font-family:"Open Sans",sans-serif;font-size:8.5px;line-height:11px;font-weight:700;white-space:normal}
.prod p{left:116px;width:114px;top:46px;text-align:center;font-size:6.8px;line-height:11px;color:#444;white-space:normal}
.prod .btn{left:141px;top:107px;width:64px;height:18px;line-height:18px;font-size:6.5px}

/* measure */
.measure{left:0;top:945px;width:627px;height:400px;background:radial-gradient(circle at 30% 45%,#2b8fc2,#0f6699 70%)}
.measure h2{top:40px;width:627px;left:0;text-align:center;color:#fff;font-size:20px;font-weight:700}
.measure .rule{top:74px;background:#fff}
.event{top:85px;width:158px;height:272px;background:#fff;border:3px solid #fff;box-shadow:0 4px 10px rgba(0,0,0,.2)}
.event .img{left:0;top:0;width:152px;height:107px;background:linear-gradient(180deg,#aac4d4,#52616f)}
.event h3{left:6px;width:140px;top:120px;text-align:center;font-family:"Open Sans",sans-serif;font-size:7.5px;line-height:11px;font-weight:700;white-space:normal}
.event p{left:10px;width:132px;top:148px;text-align:center;font-size:7px;line-height:11px;color:#444;white-space:normal}
.event .t{left:34px;top:204px;width:84px;height:18px;line-height:18px;font-size:6.5px}
.event .d{left:34px;top:228px;width:84px;height:18px;line-height:18px;font-size:6.5px}

/* about */
.about-photo{left:76px;top:1396px;width:215px;height:207px;background:linear-gradient(135deg,#1d3c5c,#5a9cc4)}
.about-photo2{left:159px;top:1501px;width:159px;height:133px;background:linear-gradient(135deg,#0c2f6a,#1d4f9a)}
.about h2{left:359px;top:1414px;font-size:20px;font-weight:800;color:#111}
.about .rule{left:359px;top:1447px}
.about p{left:359px;top:1462px;width:195px;font-size:6.6px;line-height:10.8px;color:#444;white-space:normal}
.about .btn{left:359px;top:1573px;width:77px;height:22px;line-height:22px;font-size:6.5px}

/* catalog */
.catalog{left:0;top:1687px;width:627px;height:290px;background:#fff}
.catalog-cut{left:0;top:0}
.book{left:76px;top:30px;width:130px;height:230px;background:linear-gradient(180deg,#1a6ea3 0 42%,#fff 42% 45%,#c7c9cc 45%);box-shadow:6px 6px 10px rgba(0,0,0,.3)}
.catalog h2{left:331px;top:46px;font-size:15px;font-weight:700;color:#fff;letter-spacing:.4px}
.catalog p{left:331px;top:74px;width:222px;font-size:6.6px;line-height:12.5px;color:#d6e4f0;white-space:normal}
.catalog .btn{left:332px;top:140px;width:127px;height:25px;line-height:25px;font-size:7px}

/* contact */
.contact{left:0;top:1977px;width:627px;height:100px;background:linear-gradient(90deg,#0f6aa3,#1a86bf)}
.c-item{top:35px}
.c-item svg{left:0;top:0}
.c-item .k{left:45px;top:2px;font-size:10px;color:#fff}
.c-item .v{left:45px;top:16px;font-size:10px;color:#fff}
.person{left:434px;top:1927px;width:122px;height:155px;border-radius:40px 40px 0 0;background:linear-gradient(180deg,#cfd3d8,#4d6a8e)}

/* footer */
.footer{left:0;top:2077px;width:627px;height:232px;background:var(--foot)}
.footer .brand{left:76px;top:40px;font-size:36px;color:var(--accent)}
.social{top:104px;width:14px;height:14px;border:1px solid #ddd;border-radius:50%}
.footer h3{top:41px;font-size:10px;font-weight:700;color:#fff;font-family:"Open Sans",sans-serif}
.footer ul{left:253px;top:64px;list-style:none}
.footer li{position:relative;display:block;font-size:6.8px;line-height:15px;color:#ccc}
.footer .nl{left:409px;top:68px;width:140px;font-size:6.6px;line-height:10px;color:#ccc;white-space:normal}
.footer .field{left:409px;top:95px;width:143px;height:18px;border-radius:9px;background:#fff;font-size:6.6px;color:#888;padding:4px 10px}
.footer .btn{left:410px;top:122px;width:75px;height:18px;line-height:18px;font-size:6.5px}
.footer .copy{left:0;width:627px;top:208px;text-align:center;font-size:7px;color:#ccc}

/* mega menu */
.mega{left:75px;top:80px;width:475px;height:139px;background:#fff;border-radius:0 0 8px 8px;box-shadow:0 6px 14px rgba(0,0,0,.25)}
.mega .col{top:14px;width:150px}
.mega h3{left:0;top:0;font-size:9.5px;font-weight:700;color:var(--deep)}
.mega ul{left:0;top:22px;list-style:none}
.mega li{position:relative;display:block;font-size:6.2px;line-height:14.6px;color:#333}
.mega li::before{content:"›";margin-right:4px}
.mega .sep{top:14px;width:1px;height:112px;background:var(--line)}
</style>
</head>
<body>

<!-- homepage -->
<div class="frame frame--home">
<div class="page">
  <header class="topbar">
    <span class="brand">KORVEN</span>
    <div class="call">
      <svg width="22" height="22" viewBox="0 0 24 24"><path d="M6.6 10.8a15 15 0 0 0 6.6 6.6l2.2-2.2a1 1 0 0 1 1-.25 11.4 11.4 0 0 0 3.6.57 1 1 0 0 1 1 1V20a1 1 0 0 1-1 1A17 17 0 0 1 3 4a1 1 0 0 1 1-1h3.5a1 1 0 0 1 1 1c0 1.25.2 2.45.57 3.57a1 1 0 0 1-.25 1z" fill="#0b4f7c"/></svg>
      <span class="lbl">Call Us Now</span>
      <span class="num">+49 (0) 987654321</span>
    </div>
    <div class="lang">
      <svg width="9" height="9" viewBox="0 0 10 10"><circle cx="5" cy="5" r="4.3" fill="none" stroke="#777" stroke-width=".8"/><path d="M.7 5h8.6M5 .7c-2 2.5-2 6.1 0 8.6M5 .7c2 2.5 2 6.1 0 8.6" fill="none" stroke="#777" stroke-width=".8"/></svg>
      <span>EN</span><i></i>
    </div>
    <svg class="search" width="12" height="12" viewBox="0 0 12 12"><circle cx="5" cy="5" r="3.8" fill="none" stroke="#888" stroke-width="1.4"/><path d="M8 8l3 3" stroke="#888" stroke-width="1.4"/></svg>
  </header>
  <nav class="nav">
    <a class="is-active" style="left:66px">HOME</a>
    <a style="left:102px">GEARBOXES &amp; MOTORS</a>
    <a style="left:196px">ENGINE COMPONENTS</a>
    <a style="left:287px">DRAWING PARTS</a>
    <a style="left:358px">MACHINES &amp; ACCESSORIES</a>
    <a style="left:463px">ABOUT US</a>
    <a style="left:510px">CONTACT</a>
  </nav>
  <section class="hero">
    <h1>YOUR COMPETENT PARTNER FOR INDUSTRIAL ENGINES</h1>
    <p class="sub">transmission and drawing parts with more than 5000 satisfied customers</p>
    <span class="btn btn--accent b1">OUR PRODUCTS</span>
    <span class="btn btn--navy b2">DOWNLOAD CATALOG</span>
    <div class="hero-visual" role="img" aria-label="Large photo of a precision gear reducer with visible planetary gears"></div>
    <svg class="arrow" style="left:52px" width="12" height="8" viewBox="0 0 12 8"><path d="M11 4H1m3-3L1 4l3 3" fill="none" stroke="#0171a1" stroke-width="1.2"/></svg>
    <div class="thumb" style="left:76px"><div role="img" aria-label="Right-angle gearbox"></div></div>
    <div class="thumb" style="left:196px"><div role="img" aria-label="Blue DC gear motor"></div></div>
    <div class="thumb thumb--active" style="left:316px"><div role="img" aria-label="Precision gear reducer"></div></div>
    <div class="thumb" style="left:436px"><div role="img" aria-label="Black motor with orange gearbox"></div></div>
    <svg class="arrow" style="left:562px" width="12" height="8" viewBox="0 0 12 8"><path d="M1 4h10M8 1l3 3-3 3" fill="none" stroke="#0171a1" stroke-width="1.2"/></svg>
  </section>

  <h2 class="section-title" style="top:526px">Our Products</h2>
  <i class="rule" style="top:558px"></i>
  <article class="prod" style="left:66px;top:589px"><div class="img" role="img" aria-label="Group of blue gear motors"></div><h3>NEMO ENIM IPSAM VOLUPTATEM</h3><p>Sed ut perspiciatis unde omnis iste natus voluptatem accusantium doloremque lam, totam rem aperiam, eaque ipsa quae ab illo</p><span class="btn btn--navy">DETAILS</span></article>
  <article class="prod" style="left:321px;top:589px"><div class="img" role="img" aria-label="Planetary gearboxes"></div><h3>NEMO ENIM IPSAM VOLUPTATEM</h3><p>Sed ut perspiciatis unde omnis iste natus voluptatem accusantium doloremque lam, totam rem aperiam, eaque ipsa quae ab illo</p><span class="btn btn--navy">DETAILS</span></article>
  <article class="prod" style="left:66px;top:743px"><div class="img" role="img" aria-label="Right-angle gearboxes"></div><h3>NEMO ENIM IPSAM VOLUPTATEM</h3><p>Sed ut perspiciatis unde omnis iste natus voluptatem accusantium doloremque lam, totam rem aperiam, eaque ipsa quae ab illo</p><span class="btn btn--navy">DETAILS</span></article>
  <article class="prod" style="left:321px;top:743px"><div class="img" role="img" aria-label="Motors with speed controller"></div><h3>NEMO ENIM IPSAM VOLUPTATEM</h3><p>Sed ut perspiciatis unde omnis iste natus voluptatem accusantium doloremque lam, totam rem aperiam, eaque ipsa quae ab illo</p><span class="btn btn--navy">DETAILS</span></article>

  <section class="measure">
    <h2>Measure Up</h2><i class="rule"></i>
    <article class="event" style="left:66px"><div class="img" role="img" aria-label="Drill machining a gear wheel"></div><h3>NEMO ENIM IPSAM QUIA VOLUPTATEM</h3><p>Sed ut perspiciatis unde omnis iste natus error sit voluptatem acctium doloremque laudantium, totam rem aperiam, eaque ipsa</p><span class="btn btn--navy t">FREE TICKET</span><span class="btn btn--sky d">DETAILS</span></article>
    <article class="event" style="left:236px;top:89px"><div class="img" role="img" aria-label="Hand holding a motor with copper windings"></div><h3 style="top:124px">NEMO ENIM IPSAM QUIA VOLUPTATEM</h3><p style="top:152px">Sed ut perspiciatis unde omnis iste natus error sit voluptatem acctium doloremque laudantium, totam rem aperiam, eaque ipsa</p><span class="btn btn--navy t">FREE TICKET</span><span class="btn btn--sky d">DETAILS</span></article>
    <article class="event" style="left:406px"><div class="img" role="img" aria-label="Lathe machining a metal part"></div><h3>NEMO ENIM IPSAM QUIA VOLUPTATEM</h3><p>Sed ut perspiciatis unde omnis iste natus error sit voluptatem acctium doloremque laudantium, totam rem aperiam, eaque ipsa</p><span class="btn btn--navy t">FREE TICKET</span><span class="btn btn--sky d">DETAILS</span></article>
  </section>

  <section class="about">
    <div class="about-photo" role="img" aria-label="Engineer working with holographic gear display"></div>
    <div class="about-photo2" role="img" aria-label="Blue gear motors on dark blue background"></div>
    <h2>ABOUT KORVEN</h2><i class="rule"></i>
    <p>Sed ut perspiciatis unde omnis iste natus error sit vatem accusantium doloremque laudantium, totam rem apeam, eaque ipsa quae ab illo inventore veritatis et quasi arccto beatae vitae dicta sunt explicabo. Nemo enim ipsam vuptatem quia voluptas sit aspernatur aut odit aut fugit, sed quia consequuntur magni dolores eos qui ratione vuptatem sequi nesciunt. Neque porro quisquam est, qui dolorem ipsum quia dolor sit amet, consectetur, adipisci velit, sed quia non numquam eius modi tempora</p>
    <span class="btn btn--accent">LEARN MORE</span>
  </section>

  <section class="catalog">
    <svg class="catalog-cut" width="627" height="290" viewBox="0 0 627 290"><defs><linearGradient id="cg1" x1="0" x2="1"><stop offset="0" stop-color="#14385e"/><stop offset="1" stop-color="#1f5a8c"/></linearGradient></defs><path d="M0 0H627V218L0 198Z" fill="url(#cg1)"/></svg>
    <div class="book" role="img" aria-label="Printed product catalog for AC and DC gear motors"></div>
    <h2>DOWNLOAD CATALOG</h2>
    <p>Sed ut perspiciatis unde omnis iste natus error sit voluptatem accusantium doloremque laudantium, totam rem aperiam, eaque ipsa quae ab illo inventore veritatis et quasi architecto beatae vitae dicta sunt explicabo.</p>
    <span class="btn btn--accent">DOWNLOAD CATALOG</span>
  </section>

  <section class="contact">
    <div class="c-item" style="left:76px"><svg width="30" height="30" viewBox="0 0 30 30"><circle cx="15" cy="15" r="14" fill="none" stroke="#fff" stroke-width="1.3"/><path d="M11 9l3 3-1.5 2a9 9 0 0 0 4 4l2-1.5 3 3-2 2c-5 0-11-6-11-11z" fill="#fff"/></svg><span class="k">Telephone:</span><span class="v">+49 (0) 987654321</span></div>
    <div class="c-item" style="left:261px"><svg width="30" height="30" viewBox="0 0 30 30"><circle cx="15" cy="15" r="14" fill="none" stroke="#fff" stroke-width="1.3"/><rect x="8" y="10" width="14" height="10" rx="1" fill="#fff"/><path d="M8 10l7 6 7-6" fill="none" stroke="#1a78b0" stroke-width="1.2"/></svg><span class="k">Email</span><span class="v">info@korven.example</span></div>
  </section>
  <div class="person" role="img" aria-label="Smiling woman sitting with a laptop"></div>

  <footer class="footer">
    <span class="brand">KORVEN</span>
    <i class="social" style="left:76px"></i><i class="social" style="left:95px"></i><i class="social" style="left:114px"></i><i class="social" style="left:133px"></i>
    <h3 style="left:253px">PRODUCTS</h3>
    <ul><li>AC DC gearmotors</li><li>AC DC right angle gearmotors</li><li>DC brushless gearmotors</li><li>Planetary gearmotors</li><li>Planetary gearboxes HD</li></ul>
    <h3 style="left:409px">SIGN UP FOR NEWSLETTER</h3>
    <p class="nl">Sed ut perspiciatis unde omnis iste natus error sit voluptatem accusntium</p>
    <span class="field">Enter email</span>
    <span class="btn btn--accent">SUBSCRIBE</span>
    <p class="copy">KORVEN © 2020 All Rights Reserved | Privacy Policy | Terms and Conditions</p>
  </footer>
</div>
</div>

<!-- homepage with open mega menu -->
<div class="frame frame--mega">
<div class="page">
  <header class="topbar">
    <span class="brand">KORVEN</span>
    <div class="call">
      <svg width="22" height="22" viewBox="0 0 24 24"><path d="M6.6 10.8a15 15 0 0 0 6.6 6.6l2.2-2.2a1 1 0 0 1 1-.25 11.4 11.4 0 0 0 3.6.57 1 1 0 0 1 1 1V20a1 1 0 0 1-1 1A17 17 0 0 1 3 4a1 1 0 0 1 1-1h3.5a1 1 0 0 1 1 1c0 1.25.2 2.45.57 3.57a1 1 0 0 1-.25 1z" fill="#0b4f7c"/></svg>
      <span class="lbl">Call Us Now</span>
      <span class="num">+49 (0) 987654321</span>
    </div>
    <div class="lang">
      <svg width="9" height="9" viewBox="0 0 10 10"><circle cx="5" cy="5" r="4.3" fill="none" stroke="#777" stroke-width=".8"/><path d="M.7 5h8.6M5 .7c-2 2.5-2 6.1 0 8.6M5 .7c2 2.5 2 6.1 0 8.6" fill="none" stroke="#777" stroke-width=".8"/></svg>
      <span>EN</span><i></i>
    </div>
    <svg class="search" width="12" height="12" viewBox="0 0 12 12"><circle cx="5" cy="5" r="3.8" fill="none" stroke="#888" stroke-width="1.4"/><path d="M8 8l3 3" stroke="#888" stroke-width="1.4"/></svg>
  </header>
  <nav class="nav">
    <a style="left:66px">HOME</a>
    <a style="left:102px">GEARBOXES &amp; MOTORS</a>
    <a class="is-active" style="left:196px">ENGINE COMPONENTS</a>
    <a style="left:287px">DRAWING PARTS</a>
    <a style="left:358px">MACHINES &amp; ACCESSORIES</a>
    <a style="left:463px">ABOUT US</a>
    <a style="left:510px">CONTACT</a>
  </nav>
  <section class="hero">
    <h1>YOUR COMPETENT PARTNER FOR INDUSTRIAL ENGINES</h1>
    <p class="sub">transmission and drawing parts with more than 5000 satisfied customers</p>
    <span class="btn btn--accent b1">OUR PRODUCTS</span>
    <span class="btn btn--navy b2">DOWNLOAD CATALOG</span>
    <div class="hero-visual" role="img" aria-label="Large photo of a precision gear reducer with visible planetary gears"></div>
    <svg class="arrow" style="left:52px" width="12" height="8" viewBox="0 0 12 8"><path d="M11 4H1m3-3L1 4l3 3" fill="none" stroke="#0171a1" stroke-width="1.2"/></svg>
    <div class="thumb" style="left:76px"><div role="img" aria-label="Right-angle gearbox"></div></div>
    <div class="thumb" style="left:196px"><div role="img" aria-label="Blue DC gear motor"></div></div>
    <div class="thumb thumb--active" style="left:316px"><div role="img" aria-label="Precision gear reducer"></div></div>
    <div class="thumb" style="left:436px"><div role="img" aria-label="Black motor with orange gearbox"></div></div>
    <svg class="arrow" style="left:562px" width="12" height="8" viewBox="0 0 12 8"><path d="M1 4h10M8 1l3 3-3 3" fill="none" stroke="#0171a1" stroke-width="1.2"/></svg>
  </section>

  <div class="mega">
    <div class="col" style="left:17px"><h3>Engine components</h3><ul><li>Morbi a orci quis ante rutrum ornare</li><li>Maecenas vehicula neque</li><li>Phasellus tincidunt est sed imperdiet</li><li>Nam aliquet nulla nec neque</li><li>Integer ut libero ac massa malesuada</li><li>Sed semper lectus placerat sapien</li></ul></div>
    <i class="sep" style="left:160px"></i>
    <div class="col" style="left:175px"><h3>Donec vel mi sollicitudin</h3><ul><li>Morbi a orci quis ante rutrum ornare</li><li>Maecenas vehicula neque</li><li>Phasellus tincidunt est sed imperdiet</li><li>Nam aliquet nulla nec neque</li><li>Integer ut libero ac massa malesuada</li><li>Sed semper lectus placerat sapien</li></ul></div>
    <i class="sep" style="left:320px"></i>
    <div class="col" style="left:335px"><h3>Donec vel mi sollicitudin</h3><ul><li>Morbi a orci quis ante rutrum ornare</li><li>Maecenas vehicula neque</li><li>Phasellus tincidunt est sed imperdiet</li><li>Nam aliquet nulla nec neque</li><li>Integer ut libero ac massa malesuada</li><li>Sed semper lectus placerat sapien</li></ul></div>
  </div>

  <h2 class="section-title" style="top:526px">Our Products</h2>
  <i class="rule" style="top:558px"></i>
  <article class="prod" style="left:66px;top:589px"><div class="img" role="img" aria-label="Group of blue gear motors"></div><h3>NEMO ENIM IPSAM VOLUPTATEM</h3><p>Sed ut perspiciatis unde omnis iste natus voluptatem accusantium doloremque lam, totam rem aperiam, eaque ipsa quae ab illo</p><span class="btn btn--navy">DETAILS</span></article>
  <article class="prod" style="left:321px;top:589px"><div class="img" role="img" aria-label="Planetary gearboxes"></div><h3>NEMO ENIM IPSAM VOLUPTATEM</h3><p>Sed ut perspiciatis unde omnis iste natus voluptatem accusantium doloremque lam, totam rem aperiam, eaque ipsa quae ab illo</p><span class="btn btn--navy">DETAILS</span></article>
  <article class="prod" style="left:66px;top:743px"><div class="img" role="img" aria-label="Right-angle gearboxes"></div><h3>NEMO ENIM IPSAM VOLUPTATEM</h3><p>Sed ut perspiciatis unde omnis iste natus voluptatem accusantium doloremque lam, totam rem aperiam, eaque ipsa quae ab illo</p><span class="btn btn--navy">DETAILS</span></article>
  <article class="prod" style="left:321px;top:743px"><div class="img" role="img" aria-label="Motors with speed controller"></div><h3>NEMO ENIM IPSAM VOLUPTATEM</h3><p>Sed ut perspiciatis unde omnis iste natus voluptatem accusantium doloremque lam, totam rem aperiam, eaque ipsa quae ab illo</p><span class="btn btn--navy">DETAILS</span></article>

  <section class="measure">
    <h2>Measure Up</h2><i class="rule"></i>
    <article class="event" style="left:66px"><div class="img" role="img" aria-label="Drill machining a gear wheel"></div><h3>NEMO ENIM IPSAM QUIA VOLUPTATEM</h3><p>Sed ut perspiciatis unde omnis iste natus error sit voluptatem acctium doloremque laudantium, totam rem aperiam, eaque ipsa</p><span class="btn btn--navy t">FREE TICKET</span><span class="btn btn--sky d">DETAILS</span></article>
    <article class="event" style="left:236px;top:89px"><div class="img" role="img" aria-label="Hand holding a motor with copper windings"></div><h3 style="top:124px">NEMO ENIM IPSAM QUIA VOLUPTATEM</h3><p style="top:152px">Sed ut perspiciatis unde omnis iste natus error sit voluptatem acctium doloremque laudantium, totam rem aperiam, eaque ipsa</p><span class="btn btn--navy t">FREE TICKET</span><span class="btn btn--sky d">DETAILS</span></article>
    <article class="event" style="left:406px"><div class="img" role="img" aria-label="Lathe machining a metal part"></div><h3>NEMO ENIM IPSAM QUIA VOLUPTATEM</h3><p>Sed ut perspiciatis unde omnis iste natus error sit voluptatem acctium doloremque laudantium, totam rem aperiam, eaque ipsa</p><span class="btn btn--navy t">FREE TICKET</span><span class="btn btn--sky d">DETAILS</span></article>
  </section>

  <section class="about">
    <div class="about-photo" role="img" aria-label="Engineer working with holographic gear display"></div>
    <div class="about-photo2" role="img" aria-label="Blue gear motors on dark blue background"></div>
    <h2>ABOUT KORVEN</h2><i class="rule"></i>
    <p>Sed ut perspiciatis unde omnis iste natus error sit vatem accusantium doloremque laudantium, totam rem apeam, eaque ipsa quae ab illo inventore veritatis et quasi arccto beatae vitae dicta sunt explicabo. Nemo enim ipsam vuptatem quia voluptas sit aspernatur aut odit aut fugit, sed quia consequuntur magni dolores eos qui ratione vuptatem sequi nesciunt. Neque porro quisquam est, qui dolorem ipsum quia dolor sit amet, consectetur, adipisci velit, sed quia non numquam eius modi tempora</p>
    <span class="btn btn--accent">LEARN MORE</span>
  </section>

  <section class="catalog">
    <svg class="catalog-cut" width="627" height="290" viewBox="0 0 627 290"><defs><linearGradient id="cg2" x1="0" x2="1"><stop offset="0" stop-color="#14385e"/><stop offset="1" stop-color="#1f5a8c"/></linearGradient></defs><path d="M0 0H627V218L0 198Z" fill="url(#cg2)"/></svg>
    <div class="book" role="img" aria-label="Printed product catalog for AC and DC gear motors"></div>
    <h2>DOWNLOAD CATALOG</h2>
    <p>Sed ut perspiciatis unde omnis iste natus error sit voluptatem accusantium doloremque laudantium, totam rem aperiam, eaque ipsa quae ab illo inventore veritatis et quasi architecto beatae vitae dicta sunt explicabo.</p>
    <span class="btn btn--accent">DOWNLOAD CATALOG</span>
  </section>

  <section class="contact">
    <div class="c-item" style="left:76px"><svg width="30" height="30" viewBox="0 0 30 30"><circle cx="15" cy="15" r="14" fill="none" stroke="#fff" stroke-width="1.3"/><path d="M11 9l3 3-1.5 2a9 9 0 0 0 4 4l2-1.5 3 3-2 2c-5 0-11-6-11-11z" fill="#fff"/></svg><span class="k">Telephone:</span><span class="v">+49 (0) 987654321</span></div>
    <div class="c-item" style="left:261px"><svg width="30" height="30" viewBox="0 0 30 30"><circle cx="15" cy="15" r="14" fill="none" stroke="#fff" stroke-width="1.3"/><rect x="8" y="10" width="14" height="10" rx="1" fill="#fff"/><path d="M8 10l7 6 7-6" fill="none" stroke="#1a78b0" stroke-width="1.2"/></svg><span class="k">Email</span><span class="v">info@korven.example</span></div>
  </section>
  <div class="person" role="img" aria-label="Smiling woman sitting with a laptop"></div>

  <footer class="footer">
    <span class="brand">KORVEN</span>
    <i class="social" style="left:76px"></i><i class="social" style="left:95px"></i><i class="social" style="left:114px"></i><i class="social" style="left:133px"></i>
    <h3 style="left:253px">PRODUCTS</h3>
    <ul><li>AC DC gearmotors</li><li>AC DC right angle gearmotors</li><li>DC brushless gearmotors</li><li>Planetary gearmotors</li><li>Planetary gearboxes HD</li></ul>
    <h3 style="left:409px">SIGN UP FOR NEWSLETTER</h3>
    <p class="nl">Sed ut perspiciatis unde omnis iste natus error sit voluptatem accusntium</p>
    <span class="field">Enter email</span>
    <span class="btn btn--accent">SUBSCRIBE</span>
    <p class="copy">KORVEN © 2020 All Rights Reserved | Privacy Policy | Terms and Conditions</p>
  </footer>
</div>
</div>

</body>
</html>
```